Belvascotravel.com web design project + logo design

Hi,

We are a Russian online tour operator - sunkettle.com

We are looking to tranmsfer our domain to belvascotravel.com. The website and logo need to be belvascoesque - we are not looking to change our functionality, but we need to make the website much more attracitve to clients, much more wild looking but at the same time remaining a professional travel company.

The main concept of the website should be innovative travel (as belvasco was an innovator). Alternatively, you could go down the artist route and go down the draw / design your own tour road.

On our website the customer is able to combine travel services (hotels, flights, Visa services, and soon chauffeur, car rental etc...) put it into their basket (the basket definitely has to look better than it is at the moment) and pay for it in one go by card.

We are also stressin our customer support with web chat, call centre etc... (call centre number at the top of the page)

We aim to provide an easy user experience, but we need to make it have some more style, so I will be waiting for what you guys can come up with.
Let me know if you have any questions - skype is: mrdolbarin

Industry/Entity Type

It Company

Requirements
Must have
• It is quite a simple task - to take the existing website sunkettle.com and belvascosize it to create belvascotravel.com, the functionality of the website will remain the same and there are not many pages in the website. Homepage, Checkout step1, Checkout step 2 (you can view both of these if you select a service) and the generic pages for T&C''s, Privacy policy etc...

IMPORTANT UPDATE

We are also looking at how the search results will look in the designs, (please do a search on our website for hotel / flight)

```html
<!DOCTYPE html>
<html lang="en">
<head>
<meta charset="utf-8">
<title>Belvascotravel.com – Home</title>
<link rel="stylesheet" href="https://fonts.googleapis.com/css2?family=Open+Sans:wght@300;400;600;700&family=Signika:wght@400;600&display=swap">
<style>
:root{
  --blue:#1a6bb8;--sky:#3fa2d8;--green:#1f8f3a;--green-d:#167a2e;
  --ink:#2b2b2b;--muted:#9a9a9a;--line:#e3e3e3;--bg:#f2f2f2;
  --foot:#252b31;--foot-d:#1f2429;--foot-text:#e6e6e6;--red:#b0222a;
}
*{box-sizing:border-box;margin:0;padding:0}
html,body{width:778px;height:1200px;overflow:hidden}
body{position:relative;font-family:"Open Sans",Arial,sans-serif;background:var(--bg);color:var(--ink)}
.abs{position:absolute}
.header{left:0;top:0;width:778px;height:90px;background:linear-gradient(#fff,#f4f4f4);border-bottom:1px solid #ddd}
.brand{font-family:"Signika",sans-serif;font-weight:600;font-size:19px;color:var(--blue);display:flex;align-items:center;gap:6px}
.brand i{width:14px;height:14px;border-radius:50%;background:var(--green);display:block}
.social{top:27px;display:flex;gap:8px;left:503px}
.social span{width:16px;height:16px;border-radius:50%;background:#555;display:block}
.call{left:580px;top:29px;width:124px;text-align:center;font-size:9px;line-height:11px;color:#3a7ab5;text-transform:uppercase}
.nav{top:63px;left:368px;display:flex;align-items:center;font-size:9.5px;font-weight:600;color:var(--blue)}
.nav a{text-decoration:none;color:inherit;margin-right:35px}
.nav .on{background:var(--green);color:#fff;padding:3px 14px;border-radius:3px;margin-right:21px}
.hero{left:0;top:90px;width:778px;height:282px;background:linear-gradient(#6fb3e4 0%,#b9dcf2 42%,#2f8fb0 58%,#d9c8a8 80%,#b69c76 100%);border-bottom:4px solid var(--blue)}
.hero-photo{left:0;top:90px;width:270px;height:278px;background:linear-gradient(160deg,#3e5a2a,#9fb38a 45%,#e8e2d6 75%,#a08662)}
.search{left:270px;top:122px;width:413px;height:209px;background:#fff}
.search-head{height:52px;background:var(--blue);color:#fff;padding:8px 12px}
.search-head h2{font-weight:400;font-size:16px;letter-spacing:.3px}
.search-head p{font-size:10.5px}
.field{position:absolute;height:20px;background:linear-gradient(#f7f7f7,#ececec);border:1px solid #e0e0e0;font-size:8.5px;color:#555;padding:4px 8px}
.field::after{content:"";position:absolute;right:0;top:0;border-top:9px solid var(--sky);border-left:9px solid transparent}
.opts{left:602px;top:254px;font-size:7.5px;line-height:12px;color:#444}
.opts b{display:inline-block;width:7px;height:7px;border:1px solid #bbb;margin-right:5px;vertical-align:-1px;font-weight:400;font-size:6px;line-height:5px}
.note{left:286px;top:298px;width:230px;font-size:7.5px;line-height:11px;color:#aaa}
.cta{left:563px;top:297px;width:107px;height:24px;background:var(--green);color:#fff;font-size:10px;font-weight:700;text-align:center;line-height:24px;border-radius:2px}
.welcome h1{position:absolute;left:93px;top:408px;font-weight:300;font-size:18px;color:var(--sky)}
.copy{font-size:8.2px;line-height:15px;color:var(--muted)}
.divider-v{left:460px;top:395px;width:1px;height:195px;background:#e2e2e2}
.ring{left:498px;top:398px;width:180px;height:180px;border-radius:50%;background:#e9e9e9;padding:5px;box-shadow:0 1px 3px rgba(0,0,0,.15)}
.ring div{width:100%;height:100%;border-radius:50%;background:linear-gradient(#9ed0ef,#d7e9f1 45%,#e9dfcb 65%,#c9b79a)}
.arrow{width:32px;height:32px;border-radius:50%;background:#333;border:3px solid #ddd}
.loc-cap{left:498px;top:588px;width:180px;text-align:center;font-size:10px;color:#333}
.services{left:0;top:626px;width:778px;height:222px;background:#fafafa;border-top:1px solid #e6e6e6}
.svc-title{left:88px;top:648px;border-left:2px solid var(--red);padding-left:10px}
.svc-title h2{font-weight:400;font-size:16px;color:#333;line-height:18px}
.svc-title p{font-size:9px;font-weight:600;color:#333}
.tabs{left:88px;top:690px;width:136px}
.tab{height:31.5px;display:flex;align-items:center;padding-left:10px;gap:10px;font-size:10.5px;font-weight:600;color:#333;background:linear-gradient(#f4f4f4,#e2e2e2);border-bottom:1px solid #d0d0d0}
.tab.on{background:var(--green);color:#fff}
.svc-body{left:224px;top:690px;width:470px;height:126px;background:#fff;border:1px solid #ececec}
.svc-text{left:239px;top:704px;width:330px}
.more{left:239px;top:795px;font-size:8.5px;font-weight:600;color:var(--blue)}
.agent{left:578px;top:658px;width:104px;height:150px;background:linear-gradient(#e8e6e3 0%,#d9c3ad 20%,#3a3f47 35%,#2a2f36 100%);border-radius:50px 50px 4px 4px}
.gallery-h{left:0;top:862px;width:778px;text-align:center;font-size:9.5px;color:#444}
.gallery-h::before,.gallery-h::after{content:"";position:absolute;top:8px;width:298px;height:1px;background:#ddd}
.gallery-h::before{left:0}.gallery-h::after{right:0}
.trip{position:absolute;top:887px;width:143px}
.trip .pic{height:90px;background:#fff;padding:3px;box-shadow:0 1px 2px rgba(0,0,0,.15)}
.trip .pic div{height:100%}
.trip h3{font-weight:400;font-size:10.5px;margin:7px 0 1px 5px;color:#333}
.trip p{font-size:7.2px;line-height:9px;color:var(--muted);margin-left:3px}
.footer{left:0;top:1033px;width:778px;height:167px;background:var(--foot)}
.col{position:absolute;top:1046px;color:var(--foot-text)}
.col h4{font-weight:400;font-size:10.5px;color:#fff;margin-bottom:9px}
.col ul{list-style:none;font-size:8px;line-height:15px;color:var(--foot-text)}
.quote{font-size:8px;line-height:13px;color:var(--foot-text)}
.quote .who{color:#47b047}
.vline{top:1070px;width:1px;height:88px;background:#3a4148}
.bottom{left:0;top:1166px;width:778px;height:34px;background:var(--foot-d);font-size:8px;color:#ddd}
</style>
</head>
<body>

<header class="abs header">
  <div class="abs brand" style="left:94px;top:58px"><i></i>belvascotravel</div>
  <div class="abs social"><span></span><span></span>
    <svg width="16" height="16" viewBox="0 0 16 16"><circle cx="8" cy="8" r="8" fill="#555"/><circle cx="7.3" cy="7.3" r="3" fill="none" stroke="#fff" stroke-width="1.4"/><path d="M9.5 9.5l2.3 2.3" stroke="#fff" stroke-width="1.6"/></svg>
  </div>
  <div class="abs call">You call, we're there<br>(866-BVTRIPS)</div>
  <nav class="abs nav"><a class="on" href="#">Home</a><a href="#">Products</a><a href="#">Blog</a><a href="#">Freebies</a><a href="#">Member Login</a></nav>
</header>

<section class="abs hero" role="img" aria-label="Tropical beach with sea and palm leaves"></section>
<div class="abs hero-photo" role="img" aria-label="Family on a wooden swing by the beach"></div>

<form class="abs search">
  <div class="search-head"><h2>FIND A PLACE TO STAY</h2><p>Lorem Ipsum est simplement du faux text Lorem Ipsum est</p></div>
</form>
<div class="field" style="left:283px;top:191px;width:207px">Where do you want to go?</div>
<div class="field" style="left:513px;top:192px;width:149px">Persons</div>
<div class="field" style="left:283px;top:223px;width:97px">Check in</div>
<div class="field" style="left:393px;top:223px;width:97px">Check Out</div>
<div class="field" style="left:513px;top:223px;width:149px">Range</div>
<div class="field" style="left:283px;top:255px;width:97px">Lorem Ipsum</div>
<div class="field" style="left:393px;top:255px;width:97px">Lorem Ipsum</div>
<div class="field" style="left:511px;top:255px;width:84px">Lorem Ipsum</div>
<div class="abs opts"><div><b></b>Обратно</div><div><b>✓</b>В одну сторону</div></div>
<p class="abs note">Lorem Ipsum est simplement du faux texte employé dans la sition et la misen page avant impression.</p>
<div class="abs cta">GET YOURS NOW</div>

<section class="welcome">
  <h1>Welcome to Belvasco Travel</h1>
  <div class="abs copy" style="left:93px;top:443px;width:350px">
    <p>Lorem Ipsum est simplement du faux texte employé dans la sition et la misen page avant impression. Le Lorem Ipsum est le faux texte standard de l'imprimerie depuis les années 1500, quand un peintre anonyme assembla ensemble des morceaux de texte pour réaliser un livre spécimen de polices de texte.</p>
    <p style="margin-top:6px">Il n'a pas fait que survivre cinq siècles, mais s'est aussi adapté à la bureautique informatique, sans que son contenu n'en soit modifié. Il a été popularisé dans les années 1960 grâce à la vente de feuilles Typeset contenant des passages du Lorem Ipsum, et, plus récemment, par son inclusion dans des applications de mise en page de texte, comme Folio Layout.</p>
  </div>
</section>
<div class="abs divider-v"></div>
<div class="abs ring"><div role="img" aria-label="Traveller relaxing in a beach chair by the sea"></div></div>
<svg class="abs arrow" style="left:488px;top:472px" viewBox="0 0 26 26"><path d="M15 8l-5 5 5 5" fill="none" stroke="#fff" stroke-width="2"/></svg>
<svg class="abs arrow" style="left:660px;top:472px" viewBox="0 0 26 26"><path d="M11 8l5 5-5 5" fill="none" stroke="#fff" stroke-width="2"/></svg>
<p class="abs loc-cap">SELECT YOUR DESIRE LOCATION</p>

<section class="abs services"></section>
<div class="abs svc-title"><h2>Our Services</h2><p>Lorem Ipsum est simplement du</p></div>
<div class="abs tabs">
  <div class="tab on"><svg width="20" height="16" viewBox="0 0 20 16"><circle cx="13" cy="2.5" r="2" fill="#fff"/><path d="M4 15l4-6 3 2 2-6 4 4M8 9l-5 1" fill="none" stroke="#fff" stroke-width="1.8"/></svg>Visa Service</div>
  <div class="tab"><svg width="20" height="16" viewBox="0 0 20 16"><path d="M1 9l18-3-3 3-15 1zM8 8l-3-4h2l5 3" fill="#444"/></svg>Flights Service</div>
  <div class="tab"><svg width="20" height="16" viewBox="0 0 20 16"><path d="M2 4v9M18 9v4M2 10h16M2 9h16v-2H7V5H2" fill="none" stroke="#444" stroke-width="1.8"/></svg>Hotel Service</div>
  <div class="tab"><svg width="20" height="16" viewBox="0 0 20 16"><path d="M4 2l12 12M16 2L4 14" stroke="#444" stroke-width="2.2"/></svg>Other Services</div>
</div>
<div class="abs svc-body"></div>
<p class="abs copy svc-text" style="line-height:14.2px">Lorem Ipsum est simplement du faux texte employé dans la sition et la misen page avant impression. Le Lorem Ipsum est le faux texte standard de l'imprimerie depuis les années 1500, quand un peintre anonyme assembla ensemble des morceaux de texte pour réaliser un livre spécimen de polices de texte. Il n'a pas fait que survivre cinq siècles, mais s'est aussi adapté à la bureautique informatique, sans que son contenu n'en soit modifié.</p>
<a class="abs more">View Detail</a>
<div class="abs agent" role="img" aria-label="Customer service agent in a suit"></div>

<h2 class="abs gallery-h" style="font-weight:400"><span style="color:#bbb;margin-right:18px">‹</span>Some Ot Our Client Trip Photos<span style="color:#bbb;margin-left:18px">›</span></h2>
<div class="trip" style="left:91px"><div class="pic"><div role="img" aria-label="Beach umbrella and loungers" style="background:linear-gradient(#6fb6e6,#cfe7f5 55%,#e9ddc4)"></div></div><h3>January Trip</h3><p>Lorem Ipsum est simplement du faux texte employé dans.</p></div>
<div class="trip" style="left:242px"><div class="pic"><div role="img" aria-label="Surfer holding a surfboard in the sea" style="background:linear-gradient(#7cc3e8,#2aa6c6 55%,#c99a6e)"></div></div><h3>March Trip</h3><p>Lorem Ipsum est simplement du faux texte employé dans.</p></div>
<div class="trip" style="left:393px"><div class="pic"><div role="img" aria-label="Group of friends cheering by a van" style="background:linear-gradient(#f0c23a,#e86a8a 55%,#d8d0c8)"></div></div><h3>August Trip</h3><p>Lorem Ipsum est simplement du faux texte employé dans.</p></div>
<div class="trip" style="left:545px"><div class="pic"><div role="img" aria-label="Child running on the beach with family" style="background:linear-gradient(#8fc6ea,#3d94c0 45%,#e6dcc5)"></div></div><h3>December Trip</h3><p>Lorem Ipsum est simplement du faux texte employé dans.</p></div>

<footer class="abs footer"></footer>
<div class="col" style="left:84px"><h4>DESTINATIONS:</h4><ul><li>Europe</li><li>North America</li><li>South America</li><li>Africa</li><li>Asia</li><li>Australia</li></ul></div>
<div class="abs vline" style="left:194px"></div>
<div class="col" style="left:236px"><h4>SITE MAP</h4><ul><li>Home</li><li>Activites</li><li>Trip Styles</li><li>Responsible Travel</li></ul></div>
<div class="abs vline" style="left:357px"></div>
<div class="col" style="left:376px;width:170px"><h4>TESTITMONIALS</h4>
  <div style="display:flex;gap:8px"><div role="img" aria-label="Reviewer portrait" style="width:30px;height:30px;flex:none;background:#8a9096;border:2px solid #fff"></div>
  <div class="quote"><div class="who">Marten Okafor</div>"Lorem ipsum dolor sit nsectetuer adipiscing elit, sed diam nummy nibh euismod.ut laoreet dolore magna aliquam rat volutpat.<br>&nbsp;Ut wisi enim ad minim."</div></div></div>
<div class="abs vline" style="left:543px"></div>
<div class="col" style="left:571px"><h4>CONTACT INFORMATIONS:</h4><ul><li>E-mail: info@belvasco-mail.net</li><li>Phone: +47 21 40 88 15</li><li>Opening hours:</li><li>Mon - Fri: 09.00 - 21.00</li><li>Sat: 12.00 - 16.00</li><li>Sun: 12.00 - 14.00</li></ul></div>
<div class="abs bottom"><span class="abs" style="left:83px;top:11px">Copyright 2013 Website Name. All Rights Reserved.</span><span class="abs" style="left:572px;top:11px">Privacy Policy | Terms &amp; Condition</span></div>

</body>
</html>
```